Corvane Card

The logo is the Spanish flag colors I want a vibrant eye catching design with the yellow / red colors over either Navy or white background or black even ,
Would like a 2D feel to the logo with another lighter color logo under it look ,

Contact Information for Business Card

Corvane Flooring
Teodor Vashkin
Main Number
Cell Number
Fax Number

Website on the side of the card somewhere

Font styles to use
Sans Serif

Colors
ec1f27
ffc214

Requirements
Must have
• 2 logos feel one is bolder and the other one underneath very light

```html
<!DOCTYPE html>
<html lang="en">
<head>
<meta charset="utf-8">
<title>Corvane Flooring Business Card</title>
<link rel="stylesheet" href="https://fonts.googleapis.com/css2?family=Ubuntu:wght@400;500;700&display=swap">
<style>
  :root {
    --brand-red: #ec1f27;
    --brand-yellow: #ffc214;
    --card-yellow: #e7b829;
    --card-black: #050505;
    --backdrop: #d9d9d7;
    --white: #ffffff;
  }
  * { box-sizing: border-box; margin: 0; padding: 0; }
  html, body {
    width: 1200px;
    height: 900px;
    overflow: hidden;
    background: var(--backdrop);
    font-family: "Ubuntu", Arial, sans-serif;
  }
  .stage {
    width: 1200px;
    height: 900px;
    display: flex;
    flex-direction: column;
    align-items: center;
    justify-content: center;
    gap: 40px;
  }
  .card {
    position: relative;
    width: 600px;
    height: 343px;
    background: var(--card-black);
    overflow: hidden;
    box-shadow: 0 10px 24px rgba(0,0,0,0.25);
  }

  /* Front */
  .card-front .brand {
    position: absolute;
    left: 0; right: 0; top: 118px;
    display: flex;
    align-items: center;
    justify-content: center;
    gap: 12px;
  }
  .brand-square {
    width: 26px;
    height: 26px;
    background: var(--brand-red);
  }
  .brand-name {
    color: var(--brand-yellow);
    font-weight: 700;
    font-size: 30px;
    letter-spacing: 2px;
    text-transform: uppercase;
  }
  .card-front .website {
    position: absolute;
    left: 0; right: 0; bottom: 48px;
    text-align: center;
    color: var(--brand-yellow);
    font-size: 17px;
    letter-spacing: 2px;
  }
  .website .prefix { color: var(--brand-red); }

  /* Back */
  .card-back .panels {
    position: absolute;
    inset: 0;
  }
  .card-back .brand {
    position: absolute;
    left: 40px;
    top: 150px;
    display: flex;
    align-items: center;
    gap: 10px;
  }
  .card-back .brand-square { width: 22px; height: 22px; }
  .card-back .brand-name { font-size: 25px; }
  .person {
    position: absolute;
    left: 330px;
    top: 48px;
  }
  .person-name {
    color: var(--brand-yellow);
    font-weight: 700;
    font-size: 19px;
    letter-spacing: 0.5px;
    text-transform: uppercase;
  }
  .person-role {
    color: var(--white);
    font-size: 14px;
    margin-top: 2px;
  }
  .contact {
    position: absolute;
    left: 422px;
    top: 182px;
    color: var(--white);
    font-size: 12.5px;
    line-height: 1.3;
  }
  .address { margin-bottom: 10px; }
  .contact-list { list-style: none; }
  .contact-list li {
    display: flex;
    align-items: center;
    gap: 8px;
    margin-bottom: 3px;
  }
  .contact-icon {
    width: 14px;
    height: 14px;
    flex: none;
  }
</style>
</head>
<body>
<main class="stage">

  <section class="card card-front" aria-label="Business card front">
    <div class="brand">
      <span class="brand-square"></span>
      <span class="brand-name">Corvane Flooring</span>
    </div>
    <p class="website"><span class="prefix">www.</span>corvaneflooring.com</p>
  </section>

  <section class="card card-back" aria-label="Business card back">
    <svg class="panels" width="600" height="343" viewBox="0 0 600 343" aria-hidden="true">
      <path d="M215 0 H600 V112 L330 150 Q300 154 284 134 Z" fill="var(--brand-red)"/>
      <path d="M600 126 V343 H420 L396 196 Q392 164 424 160 Z" fill="var(--card-yellow)"/>
    </svg>

    <div class="brand">
      <span class="brand-square"></span>
      <span class="brand-name">Corvane Flooring</span>
    </div>

    <div class="person">
      <p class="person-name">Teodor Vashkin</p>
      <p class="person-role">Managing Director</p>
    </div>

    <div class="contact">
      <p class="address">Suite 102 Street name, State,<br>Zip 2034, Country</p>
      <ul class="contact-list">
        <li>
          <svg class="contact-icon" viewBox="0 0 14 14" aria-label="Cell">
            <rect width="14" height="14" rx="2" fill="var(--brand-red)"/>
            <rect x="4.5" y="2.5" width="5" height="9" rx="1" fill="none" stroke="var(--white)" stroke-width="1.2"/>
          </svg>
          0110 111 111
        </li>
        <li>
          <svg class="contact-icon" viewBox="0 0 14 14" aria-label="Phone">
            <rect width="14" height="14" rx="2" fill="var(--brand-red)"/>
            <path d="M3 5 Q7 2 11 5 V6.5 H9 V5.5 H5 V6.5 H3 Z M4 7.5 H10 L11 11 H3 Z" fill="var(--white)"/>
          </svg>
          2222 111 222
        </li>
        <li>
          <svg class="contact-icon" viewBox="0 0 14 14" aria-label="Email">
            <rect width="14" height="14" rx="2" fill="var(--brand-red)"/>
            <rect x="3" y="4" width="8" height="6" fill="none" stroke="var(--white)" stroke-width="1.1"/>
            <path d="M3 4 L7 7.5 L11 4" fill="none" stroke="var(--white)" stroke-width="1.1"/>
          </svg>
          info@corvaneflooring.com
        </li>
      </ul>
    </div>
  </section>

</main>
</body>
</html>
```